BRAMBLEFORD CONSTRUCTIONS B-Card

I currently have a b-card design but will be removing the image (tree) from the logo and have text only.
I want the card to be classy and strong within the building and construction industry.
I will be using Spot UV on the cards as per the attached examples. I will also send through some sketched ideas that I have in mind.
The color blue is similar to the image (No. 6) attached images

Target Market(s)

middle to maturre aged.
Home Owners / Renovators and Builders

Industry/Entity Type

Construction

Contact Information for Business Card

BRAMBLEFORD CONSTRUCTIONS
Name: Gareth Pennick
Title: Project Manager
Mobile: 0427 351 804
Office: (08) 9316 5172
Address: 47C Corvell Street, Malaga WA 6090
Email: info@bramblefordhomes.com.au
PO Box: 3817 Malaga WA 6944

Colors
0592cd
33a6d7
85cae6
1b1b1b

Requirements
Must have
• 1. It must have spot UV on the front of card, maybe back of card too
• 2. I really like the blue on image 6. (or at least a really cool electric blue against the charcoal grey background)
• 3. The font must be slimline and modern. Easy to read
• 4. There must be no black used on the card... Only greys and dark charcoal greys
• 5. Use only the text from the logo "Brambleford Constructions" Not the image of the tree. I am wanting the b-cards to be more masculine.
Nice to have
• 1. I like the design concept on image 6. but happy to see what else you can do with the Spot UV
• 2. Unless you have a really cool idea of the image of the tree (from previous logo) Spot UV somewhere in the design concept thats original and different then I am keen to see what you come up with
• 3. Try changing the color of the logo eg. full white or Blue and white
• 4. Another option is to have the Brambleford Logo on the front of card with the spot UV in the background of text which we specialise in eg, Roofing, Ceiling, Insulation, Gutter Guards, Electrical, Insurance etc and we can add or reduce items as required. Similar to image 12.
Should not have
• Do not include the image of the tree from previous logo. unless you have a really cool idea of Spot UV somewhere in the design concept thats original and different.

```html
<!DOCTYPE html>
<html lang="en">
<head>
<meta charset="utf-8">
<title>Brambleford Constructions – Business Card</title>
<link rel="stylesheet" href="https://fonts.googleapis.com/css2?family=Jost:wght@300;400;500&family=Source+Sans+3:wght@400&display=swap">
<style>
  :root {
    --page-bg: #e4e2de;
    --card-white: #ffffff;
    --brand-blue: #1b5aa6;
    --pattern-light: #2466b3;
    --pattern-dark: #15508f;
    --text-charcoal: #2b2b2b;
    --text-grey: #4a4a4a;
    --rule-grey: #b9b9b9;
    --white: #ffffff;
  }
  * { box-sizing: border-box; margin: 0; padding: 0; }
  html, body { width: 1200px; height: 987px; overflow: hidden; }
  body { background: var(--page-bg); position: relative; font-family: "Jost", sans-serif; }

  .card { position: absolute; left: 299px; width: 610px; height: 348px; }

  /* Front */
  .card-front { top: 157px; background: var(--card-white); }
  .card-front .frame { position: absolute; inset: 11px; border: 3px solid var(--brand-blue); }
  .front-name-mark {
    position: absolute; left: 42px; top: 140px; width: 252px; text-align: center;
    color: var(--brand-blue); font-weight: 500; font-size: 30px; line-height: 34px;
  }
  .divider {
    position: absolute; left: 314px; top: 60px; width: 2px; height: 236px;
    background: linear-gradient(to bottom, rgba(185,185,185,0), var(--rule-grey) 25%, var(--rule-grey) 75%, rgba(185,185,185,0));
  }
  .contact { position: absolute; left: 337px; top: 66px; color: var(--text-grey); }
  .contact .person-name { font-size: 24px; font-weight: 500; color: var(--brand-blue); line-height: 1.1; }
  .contact .person-title { font-size: 18px; font-weight: 400; color: var(--text-charcoal); margin-top: 3px; }
  .contact .address { font-size: 16px; font-weight: 300; line-height: 20.5px; margin-top: 12px; }
  .contact .lines { list-style: none; margin-top: 10px; }
  .contact .lines li { display: flex; align-items: center; gap: 8px; font-size: 16px; font-weight: 300; height: 23.5px; }
  .contact .lines svg { width: 16px; height: 16px; fill: var(--brand-blue); flex: none; }

  /* Back */
  .card-back { top: 527px; background: var(--brand-blue); overflow: hidden; }
  .card-back .uv-pattern {
    position: absolute; inset: 0;
    background: linear-gradient(155deg, var(--pattern-light) 0%, var(--brand-blue) 50%, var(--pattern-dark) 100%);
  }
  .card-back .frame { position: absolute; inset: 12px; border: 2px solid var(--white); }
  .back-name-mark {
    position: absolute; left: 0; right: 0; top: 128px; text-align: center;
    color: var(--white); font-weight: 500; font-size: 40px; line-height: 44px;
  }
  .services {
    position: absolute; left: 0; right: 0; top: 268px; text-align: center;
    color: var(--white); font-family: "Source Sans 3", sans-serif; font-size: 17px; line-height: 22px;
  }
</style>
</head>
<body>

<section class="card card-front" aria-label="Business card front">
  <div class="frame"></div>
  <p class="front-name-mark">Brambleford<br>Constructions</p>
  <div class="divider"></div>
  <div class="contact">
    <p class="person-name">Gareth Pennick</p>
    <p class="person-title">Project Manager</p>
    <p class="address">47C Corvell Street<br>Malaga WA 6090<br>PO Box:3817 Malaga<br>WA 6944</p>
    <ul class="lines">
      <li>
        <svg viewBox="0 0 24 24" aria-hidden="true"><path d="M6.6 10.8a15.1 15.1 0 0 0 6.6 6.6l2.2-2.2c.3-.3.7-.4 1-.2 1.1.4 2.3.6 3.6.6.6 0 1 .4 1 1V20c0 .6-.4 1-1 1A17 17 0 0 1 3 4c0-.6.4-1 1-1h3.5c.6 0 1 .4 1 1 0 1.3.2 2.5.6 3.6.1.3 0 .7-.2 1z"/></svg>
        (08) 9316 5172
      </li>
      <li>
        <svg viewBox="0 0 24 24" aria-hidden="true"><path d="M7 1h10a2 2 0 0 1 2 2v18a2 2 0 0 1-2 2H7a2 2 0 0 1-2-2V3a2 2 0 0 1 2-2zm0 3v14h10V4zm5 15.5a1 1 0 1 0 0 2 1 1 0 0 0 0-2z"/></svg>
        0427 351 804
      </li>
      <li>
        <svg viewBox="0 0 24 24" aria-hidden="true"><path d="M2 5h20v14H2zm2 2v.5l8 5 8-5V7zm0 2.9V17h16V9.9l-8 5z"/></svg>
        info@bramblefordhomes.com.au
      </li>
    </ul>
  </div>
</section>

<section class="card card-back" aria-label="Business card back">
  <div class="uv-pattern" role="img" aria-label="Spot UV background pattern of the repeated company name set diagonally across the card"></div>
  <div class="frame"></div>
  <p class="back-name-mark">Brambleford<br>Constructions</p>
  <p class="services">Roofing | Ceiling | Insulation | Gutter Guards<br>Electrical | Insurance etc</p>
</section>

</body>
</html>
```